Bright Harbor Charity - helping the disadvantaged

I would like a new web site design for my charity BRIGHT HARBOR. The charity provides help for the disadvantaged. See current site
brightharbor.org.au for details. Please refer to the current site for information on the charity. The objectives of the charity are in the "about us" tab. You will also notice on the site that we provide information about events that we sponsor an area for this should be provided on the site.

Target Market(s)

We have two targets:
1. Individuals and Businesses that will donate money to the charity.
2. Individuals that are in need of support from the charity.

Industry/Entity Type

Charity

Requirements
Must have
• Ability for individuals to be able to understand the type of support we can provide.
Nice to have
• Our logo should be prominate on each pages
Should not have
• Should be use modern fonts

```html
<!DOCTYPE html>
<html lang="en">
<head>
<meta charset="utf-8">
<title>Bright Harbor – Charity</title>
<link href="https://fonts.googleapis.com/css2?family=Arimo:ital,wght@0,400;0,700;1,400&display=swap" rel="stylesheet">
<style>
:root{
  --page:#d2cec4;
  --panel:#f6f1e6;
  --nav-text:#9a7a1c;
  --frame:#c8c0a6;
  --logo:#7ec46a;
  --accent:#e8903a;
  --heading:#1d4a22;
  --body:#6e6a62;
  --dot:#c81818;
  --btn:#dcd7cc;
  --btn-text:#8a857a;
  --donate-a:#f6b46a;
  --donate-b:#ee8a2e;
}
*{box-sizing:border-box;margin:0;padding:0}
html,body{width:936px;height:1200px;overflow:hidden}
body{background:var(--page);font-family:"Arimo",Arial,sans-serif;position:relative;color:var(--body)}
.abs{position:absolute}
.nav{left:44px;top:20px;width:612px;height:50px;background:var(--panel);border-radius:6px 0 0 0;box-shadow:0 1px 2px rgba(0,0,0,.15)}
.nav ul{list-style:none;display:flex;padding:18px 0 0 31px;font-size:12px;color:var(--nav-text);white-space:nowrap}
.nav li+li::before{content:"|";margin:0 8.5px;color:var(--nav-text)}
.search-bar{left:657px;top:20px;width:233px;height:50px;background:var(--panel);border-radius:0 6px 0 0;box-shadow:0 1px 2px rgba(0,0,0,.15)}
.search-field{position:absolute;left:26px;top:10px;width:180px;height:26px;border-radius:13px;background:#fbf9f4;box-shadow:inset 0 1px 3px rgba(0,0,0,.25);font-size:12px;color:#555;text-align:right;padding:6px 8px 0 0}
.search-field span{border-left:1px solid #888;padding-left:3px}
.banner{left:44px;top:70px;width:845px;height:222px;background:var(--frame)}
.banner-inner{position:absolute;left:7px;top:10px;width:828px;height:202px;background:linear-gradient(90deg,#3e2a1f,#5a4030 55%,#3a271c)}
.banner-photo{position:absolute;right:0;top:0;width:330px;height:202px;background:radial-gradient(ellipse at 55% 50%,#c99a7c,#7a5440 45%,#3e2a1f 80%)}
.logo{position:absolute;left:34px;top:92px;font-size:40px;font-weight:700;color:var(--logo);letter-spacing:1px}
.content{left:44px;top:310px;width:612px;height:858px;background:var(--panel);border-radius:4px 0 0 4px;box-shadow:0 1px 3px rgba(0,0,0,.2)}
.sidebar{left:657px;top:310px;width:233px;height:858px;background:var(--panel);border-radius:0 4px 4px 0;box-shadow:0 1px 3px rgba(0,0,0,.2)}
.announce{position:absolute;left:24px;top:18px;font-size:12px;color:#222}
.announce-link{position:absolute;left:25px;top:37px;font-size:12px;color:var(--accent)}
.btn{position:absolute;width:86px;height:23px;background:var(--btn);color:var(--btn-text);font-size:12px;font-style:italic;line-height:23px;padding-left:14px;white-space:nowrap}
.rule{position:absolute;left:70px;top:60px;width:466px;border-top:1px dashed #ddd6c6}
.photo{position:absolute;box-shadow:0 3px 6px rgba(0,0,0,.35)}
.story{position:absolute;left:26px;width:545px;font-size:12.4px;line-height:17.5px}
.side-title{position:absolute;left:14px;top:14px;font-size:13px;font-weight:700;line-height:13.5px;color:var(--heading)}
.side-list{position:absolute;left:14px;top:89px;list-style:none;font-size:11.3px;color:#444;white-space:nowrap}
.side-list li{height:23px;padding-left:12px;position:relative}
.side-list li.dot::before{content:"";position:absolute;left:0;top:4px;width:6px;height:6px;border-radius:50%;background:#444}
.side-head{position:absolute;left:12px;font-size:13px;font-weight:700;color:var(--heading);padding-left:17px}
.side-head::before{content:"";position:absolute;left:0;top:2px;width:10px;height:10px;border-radius:50%;background:var(--dot)}
.donate{position:absolute;left:12px;top:666px;width:214px;height:182px;background:linear-gradient(160deg,var(--donate-a),var(--donate-b));border-radius:6px;transform:skewY(-1deg)}
.donate h3{position:absolute;left:40px;top:14px;font-size:15px;font-weight:400;color:#fff;text-decoration:underline}
.donate p{position:absolute;left:22px;top:36px;width:178px;font-size:11.4px;line-height:15px;color:#222}
.donate-btn{position:absolute;left:22px;top:99px;width:167px;height:27px;border-radius:7px;background:#2a1a10;border:1px solid #fff;color:#fff;font-size:17px;text-align:center;line-height:25px}
.donate .apply{position:absolute;left:40px;top:142px;font-size:16px;color:#fff}
.arrow{position:absolute;left:16px}
.copyright{left:538px;top:1181px;font-size:10px;font-weight:700;color:#fff;white-space:nowrap}
</style>
</head>
<body>
<nav class="abs nav"><ul><li>Home</li><li>About Us</li><li>Donate</li><li>Apply</li><li>Pledge</li><li>Nominate</li><li>Events</li><li>Contact Us</li><li>Directors</li></ul></nav>
<div class="abs search-bar"><div class="search-field"><span>Search</span></div></div>

<header class="abs banner">
  <div class="banner-inner">
    <div class="logo">BRIGHT HARBOR</div>
    <div class="banner-photo" role="img" aria-label="Photo of a smiling child dressed with angel wings in a basket"></div>
  </div>
</header>

<main class="abs content">
  <div class="announce">ANNOUNCEMENT:</div>
  <div class="announce-link">Harmony Day Information sheet &amp; Booking form</div>
  <div class="btn" style="left:298px;top:29px">Click to view</div>
  <div class="rule"></div>
  <div class="photo" role="img" aria-label="Photo of a smiling girl on a swing" style="left:62px;top:73px;width:448px;height:275px;background:linear-gradient(135deg,#6f9a4a,#b07a4c 40%,#3f7f8c 75%,#5a7f3c)"></div>
  <p class="story" style="top:366px">Harmony Day Event 2012 Harmony Celebration Day - "EVERYONE BELONGS" Date:Satyurday 24th March 2012&nbsp; Venue: Halcare Education Facilities, Ashford Road, Tamora. Time: 10am - 3 pm Harmony.Bright Harbor &amp; Halcare will be holding a multicultural market and art exhibition combined with a community harmony day being held on site at....</p>
  <div class="btn" style="left:27px;top:444px">Read more</div>
  <div class="photo" role="img" aria-label="Harmony Day banner with a row of colourful paper figures holding hands" style="left:25px;top:492px;width:533px;height:112px;background:linear-gradient(180deg,#000 55%,#1a1a1a 70%,#000)"></div>
  <p class="story" style="top:628px">Harmony Day Event 2012 Harmony Celebration Day - "EVERYONE BELONGS" Date:Satyurday 24th March 2012&nbsp; Venue: Halcare Education Facilities, Ashford Road, Tamora. Time: 10am - 3 pm Harmony.Bright Harbor &amp; Halcare will be holding a multicultural market and art exhibition combined with a community harmony day being held on site at....</p>
  <div class="btn" style="left:27px;top:707px">Read more</div>
</main>

<aside class="abs sidebar">
  <h2 class="side-title">Saturday 24th March<br>at Halcare Education<br>Facilities Ashford &amp; Jubilee<br>Roads Tamora</h2>
  <ul class="side-list">
    <li class="dot">Lots of prizes to be Won!</li>
    <li class="dot">Free Entry &amp; variety of free activities</li>
    <li class="dot">Art Exhibition</li>
    <li class="dot">Perfomance</li>
    <li class="dot">Community service Info stalls</li>
    <li class="dot">Multicultural food market stalls</li>
    <li>Multural arts &amp; craft market stalls.</li>
  </ul>
  <h3 class="side-head" style="top:265px">Art Exhibition</h3>
  <div class="photo" role="img" aria-label="Dot painting artwork in red, yellow and white" style="left:8px;top:295px;width:188px;height:126px;background:radial-gradient(circle,#d84a2a,#8a2418 60%,#e0a030)"></div>
  <div class="btn" style="left:12px;top:450px;width:85px">Read more</div>
  <h3 class="side-head" style="top:486px">Harmony Day</h3>
  <div role="img" aria-label="Colourful paper figures holding hands" style="position:absolute;left:8px;top:512px;width:188px;height:66px;background:linear-gradient(90deg,#d89a70,#e0c040,#f07ab0,#e87a30,#40b0a8)"></div>
  <div style="position:absolute;left:46px;top:589px;font-size:12.5px;font-weight:700;color:#111;white-space:nowrap">everyone Belongs</div>
  <div style="position:absolute;left:41px;top:606px;width:124px;border-top:1px solid var(--dot)"></div>
  <div class="btn" style="left:12px;top:630px;width:85px">Read more</div>
  <section class="donate">
    <svg class="arrow" style="top:15px" width="12" height="12" viewBox="0 0 12 12"><path d="M0 1l5 5-5 5zM6 1l5 5-5 5z" fill="#fff"/></svg>
    <h3>Donate</h3>
    <p>If you wish to make a donation to Bright Harbor please fill out and submit the form below or con-tact us directly.</p>
    <div class="donate-btn">Click here</div>
    <svg class="arrow" style="top:145px" width="12" height="12" viewBox="0 0 12 12"><path d="M0 1l5 5-5 5zM6 1l5 5-5 5z" fill="#fff"/></svg>
    <div class="apply">Apply</div>
  </section>
</aside>

<footer class="abs copyright">Copyright © 2012 Bright Harbor Proprietary Limited. All Rights Reserved.</footer>
</body>
</html>
```